Spring Detox sale graphics for social media

You MUST read the Brief in the WORD document and follow the instructions there. I want to create 10 social media graphics (new Instagram size 4:5 (1080 x 1350 pixels) focusing on our Mother’s Day Spring Detox Sale graphics, using any of the pics attached. Use the attached pics, NO RANDOM STOCK PHOTOGRAPHY. For the color scheme of the graphics, they should all be complementary to the product colors or feel like Spring time.

Target Market(s)

primarily women

Requirements
Must have
• the photos and text attached

```html
<!DOCTYPE html>
<html lang="en">
<head>
<meta charset="utf-8">
<title>Mother's Day Spring Detox Sale – Social Graphics</title>
<link href="https://fonts.googleapis.com/css2?family=Montserrat:wght@600&family=Oswald:wght@200;300;400;700&display=swap" rel="stylesheet">
<style>
  :root {
    --backdrop: #2a2a2a;
    --card: #ffffff;
    --ink: #262626;
    --red: #c1262f;
    --bright-red: #d52628;
    --plum: #8a3a63;
    --blue: #2f479a;
    --forest: #1f4a3d;
    --pink: #c9639b;
    --magenta: #a63a78;
    --mint: #88c4ad;
    --white: #ffffff;
    --frame-red: #efb7ba;
    --frame-plum: #d6c3cd;
    --frame-blue: #c3c8e0;
    --frame-green: #c7d3cf;
    --frame-mint: #d2e8df;
  }
  html, body {
    margin: 0;
    padding: 0;
    width: 1200px;
    height: 3119px;
    overflow: hidden;
    background: var(--backdrop);
  }
  .sheet {
    display: grid;
    grid-template-columns: 460px 460px;
    grid-auto-rows: 575px;
    column-gap: 24px;
    row-gap: 31px;
    padding: 75px 0 0 131px;
  }
  .post { display: block; width: 460px; height: 575px; }
  .post-bg { fill: var(--card); }
  .frame { fill: none; stroke-width: 1; }
  .frame-red { stroke: var(--frame-red); }
  .frame-plum { stroke: var(--frame-plum); }
  .frame-blue { stroke: var(--frame-blue); }
  .frame-green { stroke: var(--frame-green); }
  .frame-mint { stroke: var(--frame-mint); }

  .heavy { font-family: 'Oswald', sans-serif; font-weight: 700; }
  .hairline { font-family: 'Oswald', sans-serif; font-weight: 200; }
  .light { font-family: 'Oswald', sans-serif; font-weight: 300; }
  .regular { font-family: 'Oswald', sans-serif; font-weight: 400; }
  .ribbon-label { font-family: 'Montserrat', sans-serif; font-weight: 600; font-size: 44px; text-anchor: middle; }

  .c-ink { fill: var(--ink); }
  .c-red { fill: var(--red); }
  .c-bright-red { fill: var(--bright-red); }
  .c-plum { fill: var(--plum); }
  .c-blue { fill: var(--blue); }
  .c-forest { fill: var(--forest); }
  .c-pink { fill: var(--pink); }
  .c-magenta { fill: var(--magenta); }
  .c-mint { fill: var(--mint); }
  .c-white { fill: var(--white); }

  .ribbon-red { color: var(--red); }
  .ribbon-plum { color: var(--plum); }
  .ribbon-blue { color: var(--blue); }
  .ribbon-forest { color: var(--forest); }
  .ribbon-ink { color: var(--ink); }
  .ribbon-pink { color: var(--pink); }
  .ribbon-mint { color: var(--mint); }
  .defs { position: absolute; width: 0; height: 0; }
</style>
</head>
<body>
<svg class="defs" aria-hidden="true">
  <defs>
    <symbol id="ribbon" viewBox="0 0 260 47" preserveAspectRatio="none">
      <polygon fill="currentColor" points="10,0 250,0 238,23.5 250,47 10,47 22,23.5"/>
      <polygon fill="currentColor" points="0,0 6,0 18,23.5 6,47 0,47 12,23.5"/>
      <polygon fill="currentColor" points="260,0 254,0 242,23.5 254,47 260,47 248,23.5"/>
    </symbol>
  </defs>
</svg>

<main class="sheet">

  <!-- Post 1 -->
  <svg class="post" viewBox="0 0 380 475">
    <rect class="post-bg" width="380" height="475"/>
    <rect class="frame frame-red" x="22" y="20" width="336" height="436" rx="12"/>
    <text class="heavy c-red" x="57" y="96" font-size="50" textLength="260" lengthAdjust="spacingAndGlyphs">Mother’s Day</text>
    <text class="hairline c-ink" x="57" y="186" font-size="98" textLength="260" lengthAdjust="spacingAndGlyphs">SPRING</text>
    <text class="heavy c-ink" x="57" y="285" font-size="112" textLength="263" lengthAdjust="spacingAndGlyphs">DETOX</text>
    <use href="#ribbon" class="ribbon-red" x="60" y="296" width="260" height="47"/>
    <text class="ribbon-label c-white" x="190" y="336" textLength="195" lengthAdjust="spacingAndGlyphs">25% OFF</text>
    <text class="regular c-ink" x="59" y="410" font-size="66" textLength="263" lengthAdjust="spacingAndGlyphs">Everything!</text>
  </svg>

  <!-- Post 2 -->
  <svg class="post" viewBox="0 0 380 475">
    <rect class="post-bg" width="380" height="475"/>
    <rect class="frame frame-plum" x="22" y="20" width="336" height="436" rx="12"/>
    <text class="heavy c-plum" x="57" y="113" font-size="84" textLength="265" lengthAdjust="spacingAndGlyphs">25% OFF</text>
    <text class="heavy c-ink" x="57" y="165" font-size="50" textLength="265" lengthAdjust="spacingAndGlyphs">MOTHER’S DAY</text>
    <text class="hairline c-plum" x="57" y="258" font-size="102" textLength="263" lengthAdjust="spacingAndGlyphs">SPRING</text>
    <text class="heavy c-ink" x="57" y="356" font-size="112" textLength="265" lengthAdjust="spacingAndGlyphs">DETOX</text>
    <use href="#ribbon" class="ribbon-plum" x="59" y="366" width="263" height="47"/>
    <text class="ribbon-label c-white" x="194" y="406">Sale</text>
  </svg>

  <!-- Post 3 -->
  <svg class="post" viewBox="0 0 380 475">
    <rect class="post-bg" width="380" height="475"/>
    <rect class="frame frame-blue" x="22" y="20" width="336" height="436" rx="12"/>
    <text class="heavy c-blue" x="57" y="118" font-size="82" textLength="265" lengthAdjust="spacingAndGlyphs">25% OFF</text>
    <text class="heavy c-ink" x="57" y="163" font-size="44" textLength="265" lengthAdjust="spacingAndGlyphs">ALL SUPPLEMENTS</text>
    <text class="hairline c-blue" x="57" y="260" font-size="102" textLength="265" lengthAdjust="spacingAndGlyphs">SPRING</text>
    <text class="heavy c-ink" x="57" y="358" font-size="112" textLength="265" lengthAdjust="spacingAndGlyphs">DETOX</text>
    <use href="#ribbon" class="ribbon-blue" x="62" y="373" width="260" height="47"/>
    <text class="ribbon-label c-white" x="195" y="413">Sale!</text>
  </svg>

  <!-- Post 4 -->
  <svg class="post" viewBox="0 0 380 475">
    <rect class="post-bg" width="380" height="475"/>
    <rect class="frame frame-green" x="22" y="20" width="336" height="436" rx="12"/>
    <text class="heavy c-forest" x="35" y="116" font-size="82" textLength="265" lengthAdjust="spacingAndGlyphs">25% OFF</text>
    <text class="hairline c-ink" x="35" y="208" font-size="102" textLength="265" lengthAdjust="spacingAndGlyphs">SPRING</text>
    <text class="heavy c-ink" x="35" y="306" font-size="110" textLength="265" lengthAdjust="spacingAndGlyphs">DETOX</text>
    <use href="#ribbon" class="ribbon-forest" x="37" y="320" width="263" height="46"/>
    <text class="ribbon-label c-white" x="174" y="359">Sale</text>
    <text class="light c-ink" x="35" y="428" font-size="64" textLength="265" lengthAdjust="spacingAndGlyphs">Spring Reset</text>
    <text class="heavy c-ink" transform="translate(360,428) rotate(-90)" x="0" y="0" font-size="62" textLength="378" lengthAdjust="spacingAndGlyphs">SUMMER READY</text>
  </svg>

  <!-- Post 5 -->
  <svg class="post" viewBox="0 0 380 475">
    <rect class="post-bg" width="380" height="475"/>
    <rect class="frame frame-red" x="22" y="20" width="336" height="436" rx="12"/>
    <text class="heavy c-bright-red" x="57" y="103" font-size="80" textLength="265" lengthAdjust="spacingAndGlyphs">25% OFF</text>
    <text class="hairline c-ink" x="57" y="160" font-size="62" textLength="265" lengthAdjust="spacingAndGlyphs">EVERYTHING</text>
    <text class="heavy c-bright-red" x="57" y="208" font-size="50" textLength="265" lengthAdjust="spacingAndGlyphs">Mother’s Day</text>
    <text class="hairline c-ink" x="57" y="298" font-size="100" textLength="265" lengthAdjust="spacingAndGlyphs">SPRING</text>
    <text class="heavy c-bright-red" x="57" y="398" font-size="112" textLength="265" lengthAdjust="spacingAndGlyphs">DETOX</text>
    <use href="#ribbon" class="ribbon-ink" x="60" y="408" width="260" height="47"/>
    <text class="ribbon-label c-white" x="195" y="448">Sale</text>
  </svg>

  <!-- Post 6 -->
  <svg class="post" viewBox="0 0 380 475">
    <rect class="post-bg" width="380" height="475"/>
    <rect class="frame frame-plum" x="22" y="20" width="336" height="436" rx="12"/>
    <text class="heavy c-pink" x="47" y="126" font-size="82" textLength="287" lengthAdjust="spacingAndGlyphs">25% OFF</text>
    <text class="heavy c-ink" x="47" y="183" font-size="50" textLength="287" lengthAdjust="spacingAndGlyphs">MOTHER’S DAY</text>
    <use href="#ribbon" class="ribbon-pink" x="49" y="195" width="285" height="48"/>
    <text class="ribbon-label c-white" x="190" y="236">Sale</text>
    <text class="hairline c-ink" x="47" y="308" font-size="60" textLength="287" lengthAdjust="spacingAndGlyphs">FEEL AMAZING</text>
    <text class="heavy c-magenta" x="47" y="416" font-size="112" textLength="287" lengthAdjust="spacingAndGlyphs">AGAIN!</text>
  </svg>

  <!-- Post 7 -->
  <svg class="post" viewBox="0 0 380 475">
    <rect class="post-bg" width="380" height="475"/>
    <rect class="frame frame-blue" x="22" y="20" width="336" height="436" rx="12"/>
    <text class="heavy c-blue" x="47" y="116" font-size="82" textLength="285" lengthAdjust="spacingAndGlyphs">25% OFF</text>
    <text class="heavy c-ink" x="47" y="176" font-size="54" textLength="285" lengthAdjust="spacingAndGlyphs">MOTHER’S DAY</text>
    <use href="#ribbon" class="ribbon-blue" x="47" y="186" width="285" height="48"/>
    <text class="ribbon-label c-white" x="189" y="227">Sale</text>
    <text class="hairline c-ink" x="47" y="308" font-size="60" textLength="285" lengthAdjust="spacingAndGlyphs">REFRESH YOUR</text>
    <text class="heavy c-blue" x="47" y="421" font-size="131" textLength="285" lengthAdjust="spacingAndGlyphs">BODY</text>
  </svg>

  <!-- Post 8 -->
  <svg class="post" viewBox="0 0 380 475">
    <rect class="post-bg" width="380" height="475"/>
    <rect class="frame frame-mint" x="22" y="20" width="336" height="436" rx="12"/>
    <text class="heavy c-mint" x="32" y="116" font-size="82" textLength="265" lengthAdjust="spacingAndGlyphs">25% OFF</text>
    <text class="hairline c-ink" x="32" y="210" font-size="102" textLength="265" lengthAdjust="spacingAndGlyphs">SPRING</text>
    <text class="heavy c-forest" x="32" y="308" font-size="112" textLength="265" lengthAdjust="spacingAndGlyphs">DETOX</text>
    <use href="#ribbon" class="ribbon-mint" x="37" y="323" width="260" height="45"/>
    <text class="ribbon-label c-forest" x="170" y="361">Sale</text>
    <text class="light c-ink" x="32" y="423" font-size="60" textLength="265" lengthAdjust="spacingAndGlyphs">Spring Cleanse</text>
    <text class="heavy c-mint" transform="translate(360,420) rotate(-90)" x="0" y="0" font-size="62" textLength="370" lengthAdjust="spacingAndGlyphs">SUMMER GLOW</text>
  </svg>

  <!-- Post 9 -->
  <svg class="post" viewBox="0 0 380 475">
    <rect class="post-bg" width="380" height="475"/>
    <rect class="frame frame-red" x="22" y="20" width="336" height="436" rx="12"/>
    <text class="heavy c-red" x="34" y="133" font-size="84" textLength="263" lengthAdjust="spacingAndGlyphs">25% OFF</text>
    <text class="heavy c-ink" x="34" y="183" font-size="50" textLength="263" lengthAdjust="spacingAndGlyphs">MOTHER’S DAY</text>
    <use href="#ribbon" class="ribbon-red" x="37" y="195" width="260" height="46"/>
    <text class="ribbon-label c-white" x="170" y="234">Sale</text>
    <text class="hairline c-ink" x="34" y="313" font-size="76" textLength="263" lengthAdjust="spacingAndGlyphs">Detox This</text>
    <text class="heavy c-ink" x="34" y="406" font-size="98" textLength="263" lengthAdjust="spacingAndGlyphs">SPRING</text>
    <text class="heavy" transform="translate(347,408) rotate(-90)" x="0" y="0" font-size="46" textLength="340" lengthAdjust="spacingAndGlyphs"><tspan class="c-red">SHINE THIS </tspan><tspan class="c-ink">SUMMER</tspan></text>
  </svg>

  <!-- Post 10 -->
  <svg class="post" viewBox="0 0 380 475">
    <rect class="post-bg" width="380" height="475"/>
    <rect class="frame frame-plum" x="22" y="20" width="336" height="436" rx="12"/>
    <text class="heavy c-plum" x="57" y="100" font-size="80" textLength="265" lengthAdjust="spacingAndGlyphs">25% OFF</text>
    <text class="heavy c-ink" x="57" y="153" font-size="50" textLength="265" lengthAdjust="spacingAndGlyphs">MOTHER’S DAY</text>
    <use href="#ribbon" class="ribbon-plum" x="59" y="163" width="263" height="47"/>
    <text class="ribbon-label c-white" x="194" y="203">Sale</text>
    <text class="hairline c-plum" x="57" y="300" font-size="100" textLength="265" lengthAdjust="spacingAndGlyphs">SPRING</text>
    <text class="heavy c-ink" x="57" y="400" font-size="112" textLength="265" lengthAdjust="spacingAndGlyphs">DETOX</text>
    <text x="59" y="436" font-size="40" textLength="265" lengthAdjust="spacingAndGlyphs"><tspan class="light c-ink">for a </tspan><tspan class="heavy c-plum">Summer Body</tspan></text>
  </svg>

</main>
</body>
</html>
```